A start up Private Wine Label for export to Asia.

We are looking for the best graphic design for our very first wine label Corvessa Wines and would like the following requirements:

1. Black background - explore and play around the shade of black
2. Gold Shimmery Colour Font
3. Font should be a cursive classic posh that says Corvessa Wines
4. We would like the front graphic design to be simple and elegant and has a traditional classic feel to it.

Target Market(s)

Small scale to test the upper class market for export to Asia

Font styles to use
Script

Colors

Designer to choose colors to be used in the design.

Requirements
Must have
• Gold font for the label Corvessa Wines with shimmery touch to it.
• Elegant black background.
• Simple but elegant design.
• Attractive to the upper class market in Asia.
Nice to have
• Explore and play around with your imagination.

```html
<!DOCTYPE html>
<html lang="en">
<head>
<meta charset="utf-8">
<title>Corvessa Wines — Label</title>
<link rel="stylesheet" href="https://fonts.googleapis.com/css2?family=Great+Vibes&display=swap">
<style>
  :root {
    --canvas-bg: #ffffff;
    --label-black-deep: #000000;
    --label-black-soft: #272727;
    --gold-light: #f4dc7a;
    --gold-mid: #c8963f;
    --gold-dark: #8a5a1e;
    --gold-pale: #fbe9a4;
    --ornament-gold: rgba(200, 150, 80, 0.42);
    --ornament-fade: rgba(200, 150, 80, 0);
  }
  html, body {
    margin: 0;
    padding: 0;
    width: 1200px;
    height: 1200px;
    overflow: hidden;
    background: var(--canvas-bg);
  }
  .canvas {
    position: relative;
    width: 1200px;
    height: 1200px;
    background: var(--canvas-bg);
  }
  .label {
    position: absolute;
    left: 258px;
    top: 219px;
    width: 719px;
    height: 719px;
    background: linear-gradient(135deg, var(--label-black-deep) 0%, #111111 45%, var(--label-black-soft) 100%);
    overflow: hidden;
  }
  .ornament {
    position: absolute;
    left: 96px;
    width: 528px;
    height: 160px;
  }
  .ornament--top {
    top: 0;
    background: linear-gradient(180deg, var(--ornament-gold) 0%, var(--ornament-fade) 100%);
  }
  .ornament--bottom {
    bottom: 0;
    background: linear-gradient(0deg, var(--ornament-gold) 0%, var(--ornament-fade) 100%);
  }
  .brand-name {
    position: absolute;
    left: 0;
    right: 0;
    top: 292px;
    margin: 0;
    text-align: center;
    font-family: "Great Vibes", cursive;
    font-weight: 400;
    font-size: 92px;
    line-height: 1.2;
    letter-spacing: 1px;
    word-spacing: 0.3em;
    white-space: nowrap;
    background: linear-gradient(90deg, var(--gold-light) 0%, var(--gold-pale) 12%, var(--gold-mid) 35%, var(--gold-dark) 48%, var(--gold-light) 62%, var(--gold-mid) 82%, var(--gold-pale) 100%);
    -webkit-background-clip: text;
    background-clip: text;
    color: transparent;
  }
</style>
</head>
<body>
<div class="canvas">
  <section class="label">
    <div class="ornament ornament--top" role="img" aria-label="Gold lace mandala ornament hanging from the top edge"></div>
    <h1 class="brand-name">Corvessa Wines</h1>
    <div class="ornament ornament--bottom" role="img" aria-label="Gold lace mandala ornament rising from the bottom edge"></div>
  </section>
</div>
</body>
</html>
```